Website for my photography business

I need a website for my photography business, Bram Kellet Photography. I need a website that has a landing page with a cover photo of each kind of photography I do. For example, Nature, Weddings, Portraits and Architecture. I want it so that when someone comes onto my website they have to choose which kind of photography page they want to visit. So if they click on the wedding photo it will open to a page with my wedding portfolio images and a contact me button. If they choose nature photography I want them to be redirected to an e-commerce section where they can purchase prints. Architecture and Portraits should open up to their respective portfolios with about me and contact info. I like this kind of format because I want people who come to my website for a specific type of photography to be able to be directed there easily without having to look at a mix of other kinds of photography. I will provide a few files to use as placeholders. I have already purchased the bramkelletphotography.example domain name. A Wix website would be great because I am most familiar with it but I am open to anything.

Industry/Entity Type

Photographer

Number of Pages Required

5+ page

Requirements
Must have
• Landing Page and e-commerce

```html
<!DOCTYPE html>
<html lang="en">
<head>
<meta charset="utf-8">
<title>Bram Kellet Photography — Home</title>
<link href="https://fonts.googleapis.com/css2?family=Caveat:wght@500;600&family=Open+Sans:wght@400;600;700&display=swap" rel="stylesheet">
<style>
  :root{
    --board:#252525;
    --paper:#ffffff;
    --ink:#1f1f2e;
    --navy:#1b3a52;
    --navy-line:#3b3566;
    --link:#2c2c55;
    --hero-teal:#7fa08f;
    --night:#000000;
    --white:#ffffff;
  }
  *{box-sizing:border-box;margin:0;padding:0}
  html,body{width:1200px;height:1160px;overflow:hidden;background:var(--board)}
  body{position:relative;font-family:"Open Sans",Arial,sans-serif;color:var(--ink)}
  .script{font-family:"Caveat",cursive}
  .abs{position:absolute}

  /* ---------- Light layout ---------- */
  .page-light{left:35px;top:35px;width:541px;height:1006px;background:var(--paper);overflow:hidden}
  .hero{left:0;top:0;width:541px;height:274px;
    background:radial-gradient(ellipse at 72% 45%, #c9b08f 0 14%, transparent 30%),
               linear-gradient(100deg,#7aa08e 0%,#86a898 55%,#7c9d8c 100%)}
  .brand{font-family:"Caveat",cursive;font-weight:500;font-size:15px;color:var(--white);white-space:nowrap}
  .page-light .brand{left:51px;top:14px}
  .nav{display:flex;font-family:"Caveat",cursive;font-weight:600;font-size:9px;white-space:nowrap}
  .page-light .nav{left:278px;top:20px;color:var(--white)}
  .nav a{color:inherit;text-decoration:none;margin-right:19px;position:relative}
  .page-light .nav a.active{color:var(--link)}
  .page-light .nav a.active::after{content:"";position:absolute;left:-1px;right:-1px;bottom:-3px;height:1px;background:var(--link)}
  .cart{left:485px;top:22px;width:9px;height:8px}
  .hero-title{left:50px;top:101px;font-family:"Caveat",cursive;font-weight:600;font-size:28px;color:var(--white);white-space:nowrap}
  .hero-lede{left:50px;top:135px;width:200px;font-size:7.2px;line-height:11.4px;color:var(--white)}

  .card-index{font-size:5.5px;font-weight:700;color:var(--link)}
  .card-photo{width:208px;height:238px}
  .card-title{width:208px;text-align:center;font-family:"Caveat",cursive;font-weight:500;font-size:16px;color:var(--ink)}
  .card-more{width:208px;text-align:center;font-size:5.6px;font-weight:700;color:var(--link)}

  .tone-portrait{background:linear-gradient(160deg,#4a4a4a 0%,#8a8a8a 35%,#c8c8c8 55%,#6e6e6e 80%,#3c3c3c 100%)}
  .tone-architecture{background:linear-gradient(180deg,#d6dbe0 0%,#c9c3b8 22%,#a4583f 45%,#8c4a36 65%,#b9b2a6 85%,#8d8a85 100%)}
  .tone-nature{background:radial-gradient(ellipse at 48% 55%,#d7782e 0 18%,transparent 32%),
               linear-gradient(180deg,#2b3a2a 0%,#3e4d35 45%,#e8ecf0 75%,#f4f6f8 100%)}
  .tone-wedding{background:radial-gradient(ellipse at 52% 40%,#1f2640 0 20%,transparent 34%),
               linear-gradient(140deg,#8d7b6a 0%,#a89580 35%,#6c6660 65%,#9b8a78 100%)}

  .footer{left:0;top:951px;width:541px;height:55px;background:var(--navy);border-top:2px solid var(--navy-line)}
  .legal{font-size:5.4px;color:var(--white);white-space:nowrap}
  .legal b{font-weight:700}
  .page-light .legal{left:52px;top:23px}
  .social-links{left:294px;top:19px;display:flex;font-size:8px;font-weight:600;color:var(--white)}
  .social-links span{margin-right:38px}
  .code{font-size:5.4px;color:var(--white)}
  .page-light .code{left:524px;top:24px}

  /* ---------- Dark layout ---------- */
  .page-dark{left:619px;top:35px;width:541px;height:321px;background:var(--night);overflow:hidden}
  .page-dark .brand{left:50px;top:13px;font-size:17px}
  .page-dark .nav{left:288px;top:28px;color:var(--white)}
  .page-dark .nav a{margin-right:19px}
  .page-dark .nav a.active::after{content:"";position:absolute;left:0;right:0;bottom:-3px;height:1.3px;background:var(--white)}
  .tile{position:absolute}
  .tag{position:absolute;width:90px;height:29px;background:var(--white);display:flex;align-items:center;justify-content:center;
       font-family:"Caveat",cursive;font-weight:500;font-size:12.5px;color:var(--ink)}
  .dots{left:258px;top:300px;display:flex;gap:2px}
  .dots i{display:block;width:5px;height:5px;border-radius:50%;background:var(--white)}
  .page-dark .legal{left:339px;top:300px}
  .page-dark .code{left:520px;top:301px}
</style>
</head>
<body>

<!-- Light home layout -->
<section class="page-light abs">
  <div class="hero abs" role="img" aria-label="Hero photo: a young girl in glasses holding a vintage camera against a soft green wall"></div>
  <div class="brand abs">Bram Kellet Photography</div>
  <nav class="nav abs">
    <a class="active" href="#">Home</a><a href="#">Portfolio</a><a href="#">Gallery</a><a href="#">About Us</a><a href="#">Contact Us</a>
  </nav>
  <svg class="cart abs" viewBox="0 0 9 8" aria-label="Cart"><path d="M0 .6h1.6l1.2 4.6h4.8L8.6 1.6H2.2" fill="none" stroke="#fff" stroke-width="1"/><circle cx="3.3" cy="7" r=".8" fill="#fff"/><circle cx="7" cy="7" r=".8" fill="#fff"/></svg>
  <h1 class="hero-title abs">Bram Kellet Photography</h1>
  <p class="hero-lede abs">Lorem ipsum dolor sit amet, consectetur adipiscing elit, sed do eiusmod tempor incididunt ut labore</p>

  <div class="card-index abs" style="left:54px;top:338px">01</div>
  <div class="card-photo tone-portrait abs" style="left:50px;top:348px" role="img" aria-label="Black and white portrait study of folded arms"></div>
  <div class="card-title abs" style="left:50px;top:590px">Portraits</div>
  <div class="card-more abs" style="left:50px;top:614px">See More</div>

  <div class="card-index abs" style="left:285px;top:311px">02</div>
  <div class="card-photo tone-architecture abs" style="left:282px;top:321px" role="img" aria-label="Brick and glass campus building with a patrol car parked in front"></div>
  <div class="card-title abs" style="left:282px;top:563px">Architecture</div>
  <div class="card-more abs" style="left:282px;top:587px">See More</div>

  <div class="card-index abs" style="left:54px;top:629px">03</div>
  <div class="card-photo tone-nature abs" style="left:50px;top:640px" role="img" aria-label="Red fox sitting on snow among pine trees"></div>
  <div class="card-title abs" style="left:50px;top:881px">Nature</div>
  <div class="card-more abs" style="left:50px;top:905px">See More</div>

  <div class="card-index abs" style="left:285px;top:602px">04</div>
  <div class="card-photo tone-wedding abs" style="left:282px;top:612px" role="img" aria-label="Two wedding rings resting on a speckled granite rock"></div>
  <div class="card-title abs" style="left:282px;top:854px">Weddings</div>
  <div class="card-more abs" style="left:282px;top:878px">See More</div>

  <footer class="footer abs">
    <p class="legal abs">© Copyrights 2020 <b>Bram Kellet Photography</b> &nbsp;|&nbsp; All Rights Reserved</p>
    <div class="social-links abs"><span>Framecast</span><span>Lenslog</span><span>Chirpline</span></div>
    <p class="code abs">C43</p>
  </footer>
</section>

<!-- Dark home layout -->
<section class="page-dark abs">
  <div class="brand abs">Bram Kellet Photography</div>
  <nav class="nav abs">
    <a class="active" href="#">Home</a><a href="#">Portfolio</a><a href="#">Gallery</a><a href="#">About Us</a><a href="#">Contact Us</a>
  </nav>

  <div class="tile tone-portrait" style="left:50px;top:72px;width:104px;height:173px" role="img" aria-label="Black and white portrait study of folded arms"></div>
  <div class="tag" style="left:122px;top:72px">Portraits</div>

  <div class="tile tone-wedding" style="left:160px;top:107px;width:103px;height:173px" role="img" aria-label="Two wedding rings resting on a speckled granite rock"></div>
  <div class="tag" style="left:232px;top:251px">Weddings</div>

  <div class="tile tone-architecture" style="left:269px;top:83px;width:103px;height:154px" role="img" aria-label="Brick and glass campus building with a patrol car parked in front"></div>
  <div class="tag" style="left:283px;top:146px">Architecture</div>

  <div class="tile tone-nature" style="left:380px;top:71px;width:103px;height:174px" role="img" aria-label="Red fox sitting on snow among pine trees"></div>
  <div class="tag" style="left:379px;top:245px">Nature</div>

  <div class="dots abs" aria-label="Social links"><i></i><i></i><i></i><i></i></div>
  <p class="legal abs">© Copyrights 2020 <b>Bram Kellet Photography</b> &nbsp;|&nbsp; All Rights Reserved</p>
  <p class="code abs">C43</p>
</section>

</body>
</html>
```